Tidewake 2021 30th Anniversary

I need a graphic designer to create our event collateral. Including A3 poster design, DL flyer design , social media tiles (instagram and FB) and web banner. Tidewake is celebrating it's 30th year anniversary. The event will be held Fri 1 Oct - Sunday 3rd Oct 2021. The council is located in the Eyre Peninsula in South Australia. We are known for our world class Oysters. I have attached an old poster from previous years. I want to really modernise the design. The A3 poster design will need to be able to be amended so I can continue to add sponsorship logos. Link to FB for further information on the event https://www.example-social.test/MarlowTidewake. I have included the current Tidewake logo and Council logo. A poster from 2018 has been included. I am not looking to include any images from previous events. I want a completely new design, bright in colour to attract readers to print advertisements etc I have also attached a design which we had a bit of a play with ourselves but are looking for a more professional design.

Brief - 30th Anniversary Friday 1st October – Sunday 3rd 2021
- Oyster Capital of Australia
- World Class Oyster’s and Specialty Cuisines
- Premier Wine, Craft Beers & Cocktails
- Live Entertainment
- Side Show Alley
- Kid’s Corner
- Artisan markets
- Fireworks display
- Social media handles FB: @MarlowTidewake
Insta: @MarlowTideWake

Requirements
Must have
• Social media handles
Dates of event
Ability to amend sponsorship/add sponsorship logos
Bright colours
Fit the profile of the region (seaside, seafood etc)
Nice to have
• Colour scheme similar to Tidewake logo provided

```html
<!DOCTYPE html>
<html lang="en">
<head>
<meta charset="utf-8">
<title>Tidewake 2021 – 30th Anniversary</title>
<link rel="stylesheet" href="https://fonts.googleapis.com/css2?family=Kaushan+Script&family=Montserrat:wght@400;600;700&family=Oswald:wght@500;700&display=swap">
<style>
  :root {
    --orange: #e0502b;
    --teal: #1d8a9e;
    --navy: #1c3f66;
    --white: #ffffff;
    --ink: #2b2b2b;
    --footer: #2f2f2f;
    --blue-1: #5b95c6;
    --blue-2: #3f7db2;
    --blue-3: #1f5c8d;
  }
  * { margin: 0; padding: 0; box-sizing: border-box; }
  html, body { width: 848px; height: 1200px; overflow: hidden; background: var(--white); }
  .poster { position: relative; width: 848px; height: 1200px; font-family: "Montserrat", sans-serif; color: var(--ink); }

  .masthead { position: absolute; top: 0; left: 0; width: 848px; height: 133px; display: flex; justify-content: space-between; align-items: center; padding: 0 50px; }
  .brand { display: flex; align-items: center; gap: 12px; font-weight: 700; font-size: 44px; color: var(--teal); letter-spacing: 0.5px; }
  .brand-dot { width: 52px; height: 52px; border-radius: 50%; background: var(--orange); }
  .council { display: flex; align-items: center; gap: 10px; font-weight: 600; font-size: 13px; color: var(--navy); }
  .council-dot { width: 56px; height: 56px; border-radius: 50%; background: #f5c41a; }

  .hero { position: absolute; top: 133px; left: 0; width: 848px; height: 383px; background: var(--orange); overflow: hidden; }
  .hero-photo { position: absolute; left: 0; top: 18px; width: 388px; height: 345px; background: radial-gradient(ellipse at 45% 50%, #e9e3d8 0%, #bfb6a6 55%, #8c8172 100%); }
  .hero-frame { position: absolute; left: 14px; top: 18px; width: 310px; height: 345px; border: 4px solid var(--white); }
  .hero-copy { position: absolute; left: 400px; top: 0; width: 448px; height: 383px; color: var(--white); text-align: center; }
  .anniv { position: absolute; left: 6px; top: 22px; display: flex; align-items: center; gap: 4px; }
  .anniv-num { font-family: "Kaushan Script", cursive; font-size: 66px; line-height: 1; }
  .anniv-lines { text-align: left; font-family: "Oswald", sans-serif; }
  .anniv-label { font-weight: 500; font-size: 29px; letter-spacing: 1px; line-height: 1.15; }
  .anniv-date { font-weight: 700; font-size: 34px; letter-spacing: 1px; line-height: 1.1; }
  .capital { position: absolute; left: 0; width: 448px; top: 130px; font-family: "Kaushan Script", cursive; font-size: 64px; font-weight: 400; line-height: 1; }
  .country { position: absolute; left: 0; width: 448px; top: 220px; font-size: 34px; font-weight: 400; letter-spacing: 1px; }
  .tagline { position: absolute; left: 0; width: 448px; top: 292px; font-size: 22px; font-weight: 400; line-height: 1.45; }

  .features { position: absolute; top: 516px; left: 0; width: 848px; height: 352px; display: grid; grid-template-columns: 424px 424px; grid-template-rows: repeat(3, 117.33px); }
  .feature { display: flex; align-items: center; justify-content: center; font-family: "Kaushan Script", cursive; font-size: 31px; color: var(--white); text-align: center; line-height: 1.2; }
  .feature.row-1 { background: linear-gradient(160deg, #6aa3d0, var(--blue-1)); }
  .feature.row-2 { background: linear-gradient(160deg, #4e8cbf, var(--blue-2)); }
  .feature.row-3 { background: linear-gradient(160deg, #2b6b9c, var(--blue-3)); }
  .feature:nth-child(even) { border-left: 1px solid rgba(255,255,255,0.08); }

  .sponsors { position: absolute; top: 868px; left: 0; width: 848px; height: 294px; padding: 28px 40px 0; }
  .sponsor-row { display: grid; grid-auto-flow: column; grid-auto-columns: 1fr; column-gap: 12px; align-items: center; height: 62px; margin-bottom: 33px; }
  .sponsor { font-weight: 700; font-size: 11px; line-height: 1.25; color: var(--navy); display: flex; align-items: center; justify-content: center; gap: 5px; text-align: center; min-width: 0; }
  .sponsor-mark { flex: none; width: 12px; height: 12px; background: var(--orange); }

  .footer { position: absolute; bottom: 0; left: 0; width: 848px; height: 38px; background: var(--footer); color: var(--white); display: flex; align-items: center; padding: 0 46px; font-size: 13px; font-weight: 600; white-space: nowrap; }
  .tickets { margin-right: auto; }
  .social { display: flex; align-items: center; gap: 8px; margin-left: 28px; font-size: 15px; }
  .social-dot { width: 22px; height: 22px; border-radius: 50%; background: #555; }
</style>
</head>
<body>
<main class="poster">
  <header class="masthead">
    <div class="brand"><span class="brand-dot"></span>Tidewake</div>
    <div class="council"><span class="council-dot"></span>Marlow District Council</div>
  </header>

  <section class="hero">
    <div class="hero-photo" role="img" aria-label="Plate of fresh oysters on the half shell with a small bowl of dipping sauce"></div>
    <div class="hero-frame"></div>
    <div class="hero-copy">
      <div class="anniv">
        <span class="anniv-num">30</span>
        <div class="anniv-lines">
          <div class="anniv-label">TH ANNIVERSARY</div>
          <div class="anniv-date">OCTOBER 1-3, 2021</div>
        </div>
      </div>
      <h1 class="capital">Oyster Capital</h1>
      <div class="country">OF AUSTRALIA</div>
      <p class="tagline">WORLD CLASS OYSTER'S AND<br>SPECIALTY CUISINES</p>
    </div>
  </section>

  <section class="features">
    <div class="feature row-1" role="img" aria-label="Blue-tinted photo of wine glasses by the sea">Premier Wine, Craft<br>Beers and Cocktails</div>
    <div class="feature row-1" role="img" aria-label="Blue-tinted photo of paper planes and kids' crafts">Kid's Corner</div>
    <div class="feature row-2" role="img" aria-label="Blue-tinted photo of market stall tents">Artisan Market</div>
    <div class="feature row-2" role="img" aria-label="Blue-tinted photo of carnival rides">Side Show Alley</div>
    <div class="feature row-3" role="img" aria-label="Blue-tinted photo of concert stage lights">Live Entertainment</div>
    <div class="feature row-3" role="img" aria-label="Blue-tinted photo of fireworks in the night sky">Fireworks Display</div>
  </section>

  <section class="sponsors" aria-label="Sponsors">
    <div class="sponsor-row">
      <span class="sponsor">Coastline Herald</span>
      <span class="sponsor">Pipi Bay Park</span>
      <span class="sponsor">Corner Grocer</span>
      <span class="sponsor"><span class="sponsor-mark"></span>Bay Traders</span>
      <span class="sponsor">Fieldhands</span>
      <span class="sponsor">State Environment Office</span>
      <span class="sponsor">Hallam Freight</span>
    </div>
    <div class="sponsor-row">
      <span class="sponsor">Harbour Works</span>
      <span class="sponsor">Keel Cover</span>
      <span class="sponsor">Brandt Realty</span>
      <span class="sponsor">Allround Group</span>
      <span class="sponsor">Stone &amp; Set</span>
      <span class="sponsor">Westreach Shellfish</span>
      <span class="sponsor">Ridgevale Vintners</span>
      <span class="sponsor">Norrin Safety</span>
    </div>
    <div class="sponsor-row">
      <span class="sponsor">Hirewell</span>
      <span class="sponsor">Fenwick Pest</span>
      <span class="sponsor">Marlow Visitor Centre</span>
      <span class="sponsor">Reefline Supplies</span>
      <span class="sponsor">Marlow Recycling</span>
      <span class="sponsor">Marlow Machinery</span>
      <span class="sponsor">Saltwing Air</span>
      <span class="sponsor">Gull Point Eco Tours</span>
    </div>
  </section>

  <footer class="footer">
    <span class="tickets">Tickets available via www.tickets-example.test/</span>
    <span class="social"><span class="social-dot"></span>@MarlowTidewake</span>
    <span class="social"><span class="social-dot"></span>@MarlowTideWake</span>
  </footer>
</main>
</body>
</html>
```